Full Business Set-Up Stationary, Folder, Envelope, & Business Card, etc. CPA Firm
CPA Firm Collarteral Package
Full Business Set-Up Stationary, Folder, Envelope, & Business Card, etc. CPA Firm - Consulting
Creative Brief
Bright & Fun-filled
Mara Benton, CPA
Certified Public Accountant
512 Wexford Lane Suite 200 Brandon, FL 33571
MaraBenton@ledgerwisemail.com
www.MaraBentonCPA-example.com
AC58163
Key Words: CPA since 1999 Servicing State of Florida since 1999 Certified Management Accountant Certified Public Accounting Firm Award Winning CPA Award Winning Professional Officies Located in the Hillcrest Merchants Guild Building Trustworthy, Professional, Experienced
Tag Line: See the Clear Path Steadfast Services
marabenton marabenton
Thanks for your submissions. Please include portfolio for the Firm. Particularly a Business Folder and Letterhead/Envelope. Ipad and Iphone Designs.

```html
<!DOCTYPE html>
<html lang="en">
<head>
<meta charset="utf-8">
<title>Mara Benton CPA — Business Card</title>
<link rel="stylesheet" href="https://fonts.googleapis.com/css2?family=Cinzel:wght@400;600&family=Libre+Baskerville&display=swap">
<style>
  :root {
    --backdrop: #8c8c8e;
    --card-white: #ffffff;
    --blue-deep: #1f63c2;
    --blue-mid: #3c8fe6;
    --blue-light: #6fb4f5;
    --brand-blue: #2a6fc9;
    --accent-green: #7cc242;
    --ink: #2b2b2b;
    --muted: #8a9a8a;
  }
  * { box-sizing: border-box; margin: 0; padding: 0; }
  html, body { width: 1200px; height: 908px; overflow: hidden; }
  body { background: var(--backdrop); position: relative; font-family: "Libre Baskerville", serif; }

  .card {
    position: absolute; width: 630px; height: 360px; border-radius: 18px; overflow: hidden;
    box-shadow: 0 10px 24px rgba(0,0,0,.28);
  }

  /* Reverse side */
  .card-back {
    left: 90px; top: 70px;
    background: radial-gradient(circle at 70% 40%, var(--blue-light) 0%, var(--blue-mid) 35%, var(--blue-deep) 100%);
  }
  .card-back .back-mark { position: absolute; right: 24px; top: 70px; }
  .card-back .wordmark {
    position: absolute; left: 46px; top: 112px; color: #fff;
    font-family: "Cinzel", serif; font-weight: 600; font-size: 32px; letter-spacing: .5px;
    white-space: nowrap;
  }
  .card-back .tagline {
    position: absolute; left: 48px; top: 158px; color: #fff;
    font-family: "Cinzel", serif; font-size: 12px; letter-spacing: 4px;
  }

  /* Front side */
  .card-front { left: 480px; top: 478px; background: var(--card-white); }
  .card-front .front-mark { position: absolute; right: 30px; top: 44px; }
  .card-front .title {
    position: absolute; right: 30px; top: 180px; color: var(--muted);
    font-family: "Cinzel", serif; font-size: 11px; letter-spacing: 1.5px; white-space: nowrap;
  }
  .card-front .green-block { position: absolute; left: 150px; top: 98px; width: 40px; height: 22px; background: var(--accent-green); }
  .card-front .wordmark {
    position: absolute; left: 200px; top: 82px; color: var(--brand-blue);
    font-family: "Cinzel", serif; font-weight: 600; font-size: 26px; letter-spacing: .3px;
    white-space: nowrap;
  }
  .card-front .tagline {
    position: absolute; left: 202px; top: 118px; color: var(--ink);
    font-family: "Cinzel", serif; font-size: 9px; letter-spacing: 3.5px;
  }
  .card-front .brand-dot { position: absolute; left: 60px; top: 170px; }
  .contact { position: absolute; left: 150px; top: 154px; color: var(--ink); font-size: 12px; line-height: 1.35; }
  .contact .license { font-size: 10px; color: var(--brand-blue); margin-bottom: 3px; }
  .card-front .blue-bar { position: absolute; left: 150px; top: 218px; width: 260px; height: 22px; background: var(--brand-blue); }
  .contact-list { list-style: none; position: absolute; left: 150px; top: 250px; font-size: 12px; color: var(--ink); line-height: 1.6; }
  .contact-list li { display: flex; align-items: center; gap: 7px; }
  .contact-list svg { flex: none; }
</style>
</head>
<body>

<section class="card card-back" aria-label="Card reverse">
  <svg class="back-mark" width="170" height="170" viewBox="0 0 170 170" aria-hidden="true">
    <circle cx="85" cy="85" r="82" fill="#ffffff" fill-opacity=".14"/>
  </svg>
  <div class="wordmark">MARA BENTON CPA</div>
  <div class="tagline">SEE THE CLEAR PATH</div>
</section>

<section class="card card-front" aria-label="Card front">
  <svg class="front-mark" width="120" height="120" viewBox="0 0 120 120" aria-hidden="true">
    <circle cx="60" cy="60" r="56" fill="#d9ddd9" fill-opacity=".45"/>
  </svg>
  <div class="title">CERTIFIED PUBLIC ACCOUNTANT</div>

  <span class="green-block"></span>
  <div class="wordmark">MARA BENTON CPA</div>
  <div class="tagline">SEE THE CLEAR PATH</div>

  <svg class="brand-dot" width="70" height="70" viewBox="0 0 70 70" aria-hidden="true">
    <circle cx="35" cy="35" r="30" fill="var(--brand-blue)"/>
  </svg>

  <div class="contact">
    <div class="license">License No. AC58163</div>
    <div class="address">512 Wexford Lane Suite 200<br>Corriston, NV 89999</div>
  </div>
  <span class="blue-bar"></span>

  <ul class="contact-list">
    <li><svg width="12" height="12" viewBox="0 0 12 12"><circle cx="6" cy="6" r="6" fill="var(--accent-green)"/><path d="M4 3.2l1 1.3-.6.7a4 4 0 0 0 2.4 2.4l.7-.6 1.3 1-.6 1A5 5 0 0 1 3 4z" fill="#fff"/></svg>555-301-0142</li>
    <li><svg width="12" height="12" viewBox="0 0 12 12"><circle cx="6" cy="6" r="6" fill="var(--accent-green)"/><rect x="3.5" y="3" width="5" height="6" rx=".6" fill="#fff"/></svg>555-301-0187</li>
    <li><svg width="12" height="12" viewBox="0 0 12 12"><circle cx="6" cy="6" r="6" fill="var(--accent-green)"/><rect x="3" y="4" width="6" height="4" fill="#fff"/><path d="M3 4l3 2.2L9 4" stroke="var(--accent-green)" stroke-width=".7" fill="none"/></svg>MaraBenton@ledgerwisemail.com</li>
    <li><svg width="12" height="12" viewBox="0 0 12 12"><circle cx="6" cy="6" r="6" fill="var(--accent-green)"/><circle cx="6" cy="6" r="3" fill="none" stroke="#fff" stroke-width=".9"/><path d="M3 6h6M6 3v6" stroke="#fff" stroke-width=".7"/></svg>www.MaraBentonCPA-example.com</li>
  </ul>
</section>

</body>
</html>
```